Oil and Gas Exploration and Production company needs a business card design

We need a business card design using our logo and colors in the logo. We want a mainstream design.

```html
<!DOCTYPE html>
<html lang="en">
<head>
<meta charset="utf-8">
<title>Corvan Oil &amp; Gas – Business Card</title>
<link href="https://fonts.googleapis.com/css2?family=Roboto:wght@400;500;700;900&display=swap" rel="stylesheet">
<style>
  :root {
    --bg: #3a3a3a;
    --ink: #141414;
    --gold: #d29a22;
    --white: #ffffff;
    --text: #2a2a2a;
    --card-black: #161616;
  }
  * { box-sizing: border-box; margin: 0; padding: 0; }
  html, body { width: 1200px; height: 960px; overflow: hidden; }
  body {
    background: var(--bg);
    font-family: "Roboto", Arial, sans-serif;
    position: relative;
  }
  .card {
    position: absolute;
    left: 240px;
    width: 720px;
    height: 411px;
    overflow: hidden;
    border-radius: 3px;
  }
  /* Back face */
  .card--back { top: 48px; background: var(--card-black); }
  .back__pattern {
    position: absolute; inset: 0;
    background: linear-gradient(160deg, #8a8a8a 0%, #4a4a4a 35%, #1e1e1e 65%, #121212 100%);
  }
  .back__logo {
    position: absolute; right: 60px; top: 170px;
    display: flex; align-items: center; gap: 12px;
  }
  .logo-dot { width: 26px; height: 26px; border-radius: 50%; background: var(--gold); }
  .logo-name { font-weight: 900; font-size: 40px; letter-spacing: 0.5px; line-height: 1; }
  .back__logo .logo-name { color: var(--white); }

  /* Front face */
  .card--front { top: 497px; background: var(--white); }
  .front__logo {
    position: absolute; right: 44px; top: 48px;
    display: flex; align-items: center; gap: 12px;
  }
  .front__logo .logo-name { color: var(--ink); }
  .person { position: absolute; left: 48px; top: 132px; }
  .person__name { color: var(--gold); font-weight: 700; font-size: 34px; line-height: 1.1; }
  .person__title { color: var(--text); font-size: 22px; margin-top: 2px; }
  .divider {
    position: absolute; left: 48px; right: 44px; top: 222px;
    height: 2px; background: var(--gold);
  }
  .contacts { position: absolute; left: 48px; top: 236px; list-style: none; }
  .contacts li {
    display: flex; align-items: center; gap: 10px;
    color: var(--text); font-size: 17px; height: 25px;
  }
  .contacts svg { width: 16px; height: 16px; fill: var(--gold); flex: none; }
  .address {
    position: absolute; right: 44px; top: 310px;
    text-align: right; color: var(--text); font-size: 18px; line-height: 1.35;
  }
  .band { position: absolute; left: 0; bottom: 0; width: 720px; height: 24px; }
</style>
</head>
<body>

<section class="card card--back" aria-label="Card back">
  <div class="back__pattern" role="img" aria-label="Repeating pattern of oil drop shapes fading from silver to black"></div>
  <div class="back__logo">
    <span class="logo-dot"></span>
    <span class="logo-name">Corvan Oil &amp; Gas</span>
  </div>
</section>

<section class="card card--front" aria-label="Card front">
  <div class="front__logo">
    <span class="logo-dot"></span>
    <span class="logo-name">Corvan Oil &amp; Gas</span>
  </div>

  <div class="person">
    <p class="person__name">Daniel Hale</p>
    <p class="person__title">President</p>
  </div>

  <div class="divider"></div>

  <ul class="contacts">
    <li>
      <svg viewBox="0 0 16 16" aria-hidden="true"><path d="M3 1l3 3-1.5 2a9 9 0 0 0 5.5 5.5L12 10l3 3-2 2C7 15 1 9 1 3z"/></svg>
      555 201 4830
    </li>
    <li>
      <svg viewBox="0 0 16 16" aria-hidden="true"><path d="M4 0h8a1 1 0 0 1 1 1v14a1 1 0 0 1-1 1H4a1 1 0 0 1-1-1V1a1 1 0 0 1 1-1zm1 2v10h6V2zm3 11a1 1 0 1 0 0 2 1 1 0 0 0 0-2z"/></svg>
      555 201 4831
    </li>
    <li>
      <svg viewBox="0 0 16 16" aria-hidden="true"><path d="M0 3h16v1.5L8 9 0 4.5zM0 6l8 4.5L16 6v7H0z"/></svg>
      info@corvanenergy.com
    </li>
    <li>
      <svg viewBox="0 0 16 16" aria-hidden="true"><path d="M8 0a8 8 0 1 0 0 16A8 8 0 0 0 8 0zm0 1.5c1 0 2 2 2.3 5.5H5.7C6 3.5 7 1.5 8 1.5zM1.6 7h2.6c.1-2 .5-3.7 1.2-4.8A6.5 6.5 0 0 0 1.6 7zm10.2 0h2.6a6.5 6.5 0 0 0-3.8-4.8c.7 1.1 1.1 2.8 1.2 4.8zM1.6 9a6.5 6.5 0 0 0 3.8 4.8C4.7 12.7 4.3 11 4.2 9zm4.1 0c.3 3.5 1.3 5.5 2.3 5.5s2-2 2.3-5.5zm6.1 0c-.1 2-.5 3.7-1.2 4.8A6.5 6.5 0 0 0 14.4 9z"/></svg>
      www.corvanenergy.com
    </li>
  </ul>

  <p class="address">Level 5, 120 Harbour Road<br>Brisbane, QLD 4000</p>

  <svg class="band" viewBox="0 0 720 24" preserveAspectRatio="none" aria-hidden="true">
    <polygon points="0,6 390,6 400,24 0,24" fill="var(--ink)"/>
    <polygon points="400,0 720,0 720,24 414,24" fill="var(--gold)"/>
  </svg>
</section>

</body>
</html>
```